KBT Business Cards

We require business cards for our business. We would like a matte black back to the card, with our logo centred in the middle. The front side of the card is open to design.

Target Market(s)

Clients looking for legal services (professional)

Industry/Entity Type

Legal

Contact Information for Business Card

Doran Kelbrath
Partner
Mobile: 0461 738 524
Email: doran@kbtlaw.co
Website: www.kbtlaw.co
Level 3, 118 Wendmore Street
Sydney NSW 2000

Font styles to use
Other font styles liked:
• Avenir

Colors
f04a50
ffffff
1b1b1b

Requirements
Must have
• Black back with logo included in the centre of the card.
• Our font is Avenir.

```html
<!DOCTYPE html>
<html lang="en">
<head>
<meta charset="utf-8">
<title>KBT Legal Business Cards</title>
<link rel="stylesheet" href="https://fonts.googleapis.com/css2?family=Roboto:wght@500;700&family=Lato:wght@400&display=swap">
<style>
  :root {
    --brand-red: #c0173f;
    --ink: #1b1b1b;
    --paper: #ffffff;
    --card-black: #0a0a0a;
    --backdrop: #6b6b6b;
    --rule: #555555;
  }
  * { margin: 0; padding: 0; box-sizing: border-box; }
  html, body { width: 1200px; height: 802px; overflow: hidden; }
  body { background: var(--backdrop); position: relative; font-family: "Lato", sans-serif; }

  .card {
    position: absolute;
    top: 274px;
    width: 443px;
    height: 265px;
    box-shadow: 2px 3px 6px rgba(0,0,0,0.45);
  }
  .card--front { left: 136px; background: var(--paper); }
  .card--back { left: 624px; background: var(--card-black); }

  /* front */
  .front-mark {
    position: absolute;
    left: 64px; top: 118px;
    display: flex; align-items: center; gap: 8px;
  }
  .mark-square { width: 14px; height: 14px; background: var(--brand-red); }
  .front-mark .mark-name {
    font-family: "Roboto", sans-serif; font-weight: 700;
    font-size: 30px; letter-spacing: 1px; color: var(--ink); line-height: 1;
  }
  .divider {
    position: absolute; left: 218px; top: 80px;
    width: 1px; height: 108px; background: var(--rule);
  }
  .details { position: absolute; left: 243px; top: 78px; color: var(--ink); }
  .details__name {
    font-family: "Roboto", sans-serif; font-weight: 500;
    font-size: 16px; color: var(--brand-red); line-height: 18px; letter-spacing: 0.2px;
  }
  .details__role { font-size: 12.5px; line-height: 14px; }
  .contact-list { list-style: none; margin-top: 9px; }
  .contact-list li {
    display: flex; align-items: center; gap: 5px;
    font-size: 12.5px; line-height: 16px;
  }
  .contact-list svg { width: 9px; height: 9px; flex: none; fill: var(--brand-red); }
  .details__address { margin-top: 8px; font-size: 12.5px; line-height: 15.5px; }

  /* back */
  .back-mark {
    position: absolute; left: 0; top: 0; width: 100%; height: 100%;
    display: flex; align-items: center; justify-content: center; gap: 14px;
  }
  .back-mark .mark-square { width: 20px; height: 20px; }
  .back-mark .mark-name {
    font-family: "Roboto", sans-serif; font-weight: 500;
    font-size: 26px; letter-spacing: 0.5px; color: var(--paper); line-height: 1;
  }
</style>
</head>
<body>

<section class="card card--front">
  <div class="front-mark">
    <span class="mark-square"></span>
    <span class="mark-name">KBT</span>
  </div>
  <div class="divider"></div>
  <div class="details">
    <p class="details__name">DORAN KELBRATH</p>
    <p class="details__role">Partner</p>
    <ul class="contact-list">
      <li>
        <svg viewBox="0 0 10 10" aria-hidden="true"><path d="M1 3.5C1 2 2.5 1.5 5 1.5S9 2 9 3.5V4.5H7V3.5H3V4.5H1Z"/><rect x="1.5" y="5" width="7" height="3.5" rx="0.5"/></svg>
        0461 738 524
      </li>
      <li>
        <svg viewBox="0 0 10 10" aria-hidden="true"><path d="M0.5 2H9.5V8H0.5Z M1 2.5L5 5.5L9 2.5" stroke="#fff" stroke-width="0.8"/></svg>
        doran@kbtlaw.co
      </li>
      <li>
        <svg viewBox="0 0 10 10" aria-hidden="true"><circle cx="5" cy="5" r="4.5"/><path d="M2.5 3.5Q4 2.5 5 4T7.5 6.5" stroke="#fff" stroke-width="0.8" fill="none"/></svg>
        www.kbtlaw.co
      </li>
    </ul>
    <p class="details__address">Level 3, 118 Wendmore<br>Street, Sydney NSW 2000</p>
  </div>
</section>

<section class="card card--back">
  <div class="back-mark">
    <span class="mark-square"></span>
    <span class="mark-name">KBT LEGAL</span>
  </div>
</section>

</body>
</html>
```